Brintel Works - Fast, Efficient and Gas Mainteance for Domestic, Commercial and Industrial clients

We are in the process of purchasing a new business and would like to get a new logo and business card.
Business is a gas maintenance business that also does new gas installations.
Has been established since 1988.
Services include:
Install all types of gas appliances & equipment inc. hot water units
Maintain / repair / replace all types of gas appliances & equipment

Target Market(s)

Domestic, Commercial and Industrial clients

Industry/Entity Type

Business

Contact Information for Business Card

admin@brintelworks.com.au
07 3918 4726
Brintel Works PTY LTD

Logo Text

Gas Fitting & Plumbing Maintenance Specialists

Font styles to use
Sans Serif

Requirements
Must have
• Logo
• Business name, contact number, email address, web address
• Domestic | Commercial | Industrial Est Since 1988
Nice to have
• Possibly a black card with a flame logo to one side
Should not have
• Spelling errors

```html
<!DOCTYPE html>
<html lang="en">
<head>
<meta charset="utf-8">
<title>Brintel Works – Business Card</title>
<link rel="stylesheet" href="https://fonts.googleapis.com/css2?family=Open+Sans:wght@400;600;700&family=Italianno&display=swap">
<style>
  :root {
    --brand-orange: #ef5a36;
    --mark-grey: #cbcbcc;
    --text-dark: #3d3f45;
    --text-mid: #55575c;
    --card-white: #ffffff;
    --page-bg: #e9e7e4;
  }
  * { margin: 0; padding: 0; box-sizing: border-box; }
  html, body {
    width: 1189px; height: 1200px; overflow: hidden;
    background: var(--page-bg);
    font-family: "Open Sans", Arial, sans-serif;
  }
  .card {
    position: absolute; left: 136px;
    width: 917px; height: 524px;
    background: var(--card-white);
    overflow: hidden;
  }
  .card--front { top: 45px; }
  .card--back { top: 623px; }

  .card__wave { position: absolute; inset: 0; width: 100%; height: 100%; }

  .mark-spot {
    position: absolute; border-radius: 50%;
    background: var(--mark-grey); opacity: .55;
  }
  .card--front .mark-spot { left: 30px; top: 60px; width: 160px; height: 160px; }
  .card--back .mark-spot { left: 98px; top: 132px; width: 210px; height: 210px; }

  .identity { position: absolute; white-space: nowrap; }
  .card--front .identity { left: 211px; top: 84px; }
  .card--back .identity { left: 341px; top: 280px; }

  .identity__name {
    color: var(--brand-orange); font-weight: 700; letter-spacing: .5px;
    text-transform: uppercase; line-height: 1;
  }
  .identity__suffix {
    color: var(--text-dark); font-weight: 700; text-transform: uppercase;
    margin-left: 10px; vertical-align: baseline;
  }
  .identity__tagline { color: var(--text-dark); font-weight: 600; line-height: 1.3; }
  .identity__sectors { color: var(--text-mid); font-weight: 400; letter-spacing: .3px; }
  .identity__est {
    font-family: "Italianno", cursive; color: #8a8b8f; margin-left: 14px;
  }

  .card--front .identity__name { font-size: 33px; }
  .card--front .identity__suffix { font-size: 11px; }
  .card--front .identity__tagline { font-size: 24px; margin-top: 4px; }
  .card--front .identity__sectors { font-size: 13.5px; margin-top: 4px; }
  .card--front .identity__est { font-size: 24px; }

  .card--back .identity__name { font-size: 41px; }
  .card--back .identity__suffix { font-size: 13px; }
  .card--back .identity__tagline { font-size: 28px; margin-top: 6px; }
  .card--back .identity__sectors { font-size: 15px; margin-top: 6px; }
  .card--back .identity__est { font-size: 28px; }

  .contacts {
    position: absolute; right: 62px; top: 358px;
    list-style: none; color: var(--card-white);
  }
  .contacts__item {
    display: flex; align-items: center; justify-content: flex-end;
    height: 40px; font-size: 27px; letter-spacing: .3px;
  }
  .contacts__icon {
    width: 25px; height: 25px; margin-left: 34px;
    background: var(--card-white); display: flex; align-items: center; justify-content: center;
  }
  .contacts__icon svg { width: 17px; height: 17px; }
</style>
</head>
<body>

<section class="card card--front">
  <svg class="card__wave" viewBox="0 0 917 524" preserveAspectRatio="none" aria-hidden="true">
    <path d="M0,384 C245,352 450,344 655,228 C760,170 845,155 917,155 L917,524 L0,524 Z" fill="var(--mark-grey)"/>
    <path d="M0,429 C245,389 458,373 668,251 C775,190 850,172 917,170 L917,524 L0,524 Z" fill="var(--card-white)"/>
    <path d="M0,437 C245,397 458,381 670,259 C777,198 852,180 917,178 L917,524 L0,524 Z" fill="var(--brand-orange)"/>
  </svg>

  <div class="mark-spot" role="img" aria-label="Brand mark placeholder"></div>

  <div class="identity">
    <div class="identity__name">Brintel Works<span class="identity__suffix">Pty Ltd</span></div>
    <div class="identity__tagline">Gas fitting &amp; Plumbing Specialists</div>
    <div class="identity__sectors">Domestic | Commercial | Industrial<span class="identity__est">Est Since 1988</span></div>
  </div>

  <ul class="contacts">
    <li class="contacts__item">07 3918 4726
      <span class="contacts__icon"><svg viewBox="0 0 24 24"><path d="M6 2l4 4-2 3c1 3 4 6 7 7l3-2 4 4-3 4C10 22 2 14 2 5z" fill="var(--brand-orange)"/></svg></span>
    </li>
    <li class="contacts__item">admin@brintelworks.com.au
      <span class="contacts__icon"><svg viewBox="0 0 24 24"><rect x="2" y="5" width="20" height="14" fill="var(--brand-orange)"/><path d="M2 5l10 8 10-8" fill="none" stroke="#fff" stroke-width="1.8"/></svg></span>
    </li>
    <li class="contacts__item">www.brintelworks.com.au
      <span class="contacts__icon"><svg viewBox="0 0 24 24"><circle cx="12" cy="12" r="10" fill="var(--brand-orange)"/><path d="M2 12h20M12 2c-4 5-4 15 0 20M12 2c4 5 4 15 0 20" fill="none" stroke="#fff" stroke-width="1.5"/></svg></span>
    </li>
  </ul>
</section>

<section class="card card--back">
  <div class="mark-spot" role="img" aria-label="Brand mark placeholder"></div>
  <div class="identity">
    <div class="identity__name">Brintel Works<span class="identity__suffix">Pty Ltd</span></div>
    <div class="identity__tagline">Gas fitting &amp; Plumbing Specialists</div>
    <div class="identity__sectors">Domestic | Commercial | Industrial<span class="identity__est">Est Since 1988</span></div>
  </div>
</section>

</body>
</html>
```